KESTREL HAIR STUDIO NEEDS A FLYER MADE

I’m wanting a flyer made up for a letter box drop for my hair salon.
It needs to target Men and Ladies.
I want to list my services we offer.
I also want on the flyer - (Present this flyer to receive
20% off any hair Colour Service)

Also wanting our logo, phone number and address.

I also want to our regular weekly deals on the back.
I will attach a inspirational picture for the flyer.

Industry/Entity Type

Hairdresser

Font styles to use
Serif
Sans Serif
Script

Requirements
Must have
• I want to list my services we offer
- Mens & Ladies Haircuts
- Style Cuts
- Colour Services
- Blowdry & Styling
- Up Styles
- Perming
- Chemical straightening

I also want on the flyer
Present this flyer to receive
20% off any hair Colour Service

Phone: 47208356
Address: Shop 3/214 Garrow Street, The Lindens, Harlow Bay 4812

I also want to our weekly deals on the back side.
Mens Day Wednesday
$19.00 Haircuts

Thursday Seniors Day
- Shampoo, Ladies Haircut & Blowdry $35
- Ladies Haircut & Blowdry $30
- Shampoo & Blowdry $27.00
-$5off any colour service
- Perm (includes Trim & Blowdry) $85
- Facial Waxing $10

FRIDAY HAPPY HOUR 3PM – 5PM
- Shampoo, Blow dry & Style $40.00
- Shampoo, Mens Haircut & Style $29.00
(Complimentary beverage on arrival)

BOOK NOW

Follow us on facebook
Nice to have
• Photos of our work (hair) we do.

```html
<!DOCTYPE html>
<html lang="en">
<head>
<meta charset="utf-8">
<title>Kestrel Hair Studio – Flyer</title>
<link rel="stylesheet" href="https://fonts.googleapis.com/css2?family=Montserrat:wght@400;500;600&family=Oswald:wght@500;600&family=Roboto+Slab:wght@400;700&display=swap">
<style>
  :root{
    --bg:#dedbd7;
    --paper:#ffffff;
    --ink:#000000;
    --text:#ffffff;
    --accent:#e9c9bf;
    --rule:#cfc7c4;
  }
  *{box-sizing:border-box;margin:0;padding:0}
  html,body{width:1200px;height:1200px;overflow:hidden;background:var(--bg)}
  body{position:relative;font-family:"Montserrat",sans-serif;color:var(--text)}
  .flyer{position:absolute;top:234px;width:518px;height:733px;background:var(--paper)}
  .flyer--front{left:58px}
  .flyer--back{left:625px}
  .flyer__sheet{position:absolute;left:16px;top:16px;width:487px;height:702px;background:var(--ink)}
  .abs{position:absolute}
  .photo{position:absolute}
  .photo--waves{background:linear-gradient(160deg,#b9a48f,#7c6350 55%,#2e2926)}
  .photo--brunette{background:linear-gradient(160deg,#c9bfb1,#6b5140 55%,#2a2522)}
  .photo--mens-side{background:linear-gradient(160deg,#cfc9c1,#8a6f57 45%,#1e1c1b)}
  .photo--fade-back{background:linear-gradient(160deg,#e3ddd5,#6b5443 50%,#1d1b1a)}
  .photo--fade-side{background:linear-gradient(160deg,#e5e0d9,#7a604c 50%,#1f1d1c)}
  .photo--blonde{background:linear-gradient(160deg,#d8d2c8,#ece6dc 45%,#2a2726)}
  .photo--storefront{background:linear-gradient(160deg,#b8b6b4,#6f6a67 55%,#4e4644)}
  .logo{position:absolute;background:var(--paper);display:flex;flex-direction:column;align-items:center;justify-content:center;color:var(--ink);font-family:"Montserrat",sans-serif;font-weight:500;line-height:1}
  .logo__name{font-size:36px;letter-spacing:1px}
  .logo__sub{font-size:11px;letter-spacing:4px;margin-top:7px}
  .services__title{font-family:"Roboto Slab",serif;font-weight:700;font-size:21px;letter-spacing:.2px}
  .services__list{list-style:none;font-size:12px;letter-spacing:.3px}
  .services__list li{height:20.8px;display:flex;align-items:center;gap:8px}
  .services__list svg{flex:none}
  .promo{position:absolute;border:1px solid var(--accent);display:flex;align-items:center;font-family:"Oswald",sans-serif;text-transform:uppercase}
  .promo__amount{font-weight:600;font-size:50px;letter-spacing:-1px;margin-left:17px;line-height:1}
  .promo__text{font-weight:500;font-size:20px;line-height:1.2;margin-left:14px;letter-spacing:-.2px}
  .contact{position:absolute;border:1px solid var(--accent);font-size:10px;font-weight:600}
  .contact__row{position:absolute;display:flex;align-items:center;gap:7px;white-space:nowrap}
  .contact__social{position:absolute;display:flex;align-items:center;gap:6px;font-weight:500}
  .contact__dot{width:13px;height:13px;border-radius:50%;background:var(--text)}
  .deals__title{font-family:"Roboto Slab",serif;font-weight:700;font-size:15px}
  .deals__feature{font-family:"Roboto Slab",serif;font-size:16px;line-height:1.2}
  .deals__feature b{font-weight:700;color:var(--accent)}
  .deals__feature .deals__price{color:var(--text)}
  .deals__sub{font-family:"Roboto Slab",serif;font-weight:700;font-size:12.5px}
  .price-table{position:absolute;border-collapse:collapse;font-size:9.8px;font-family:"Montserrat",sans-serif}
  .price-table td{border:1px solid var(--rule);padding:0 6px;height:21px}
  .price-table td.price{width:40px;text-align:center;font-weight:500}
  .price-table .tall td{height:33px;line-height:1.25}
</style>
</head>
<body>

<section class="flyer flyer--front">
  <div class="flyer__sheet"></div>

  <div class="photo photo--waves" style="left:26px;top:26px;width:216px;height:278px" role="img" aria-label="Photo of long wavy bronde hair styled in soft curls"></div>

  <div class="logo" style="left:253px;top:26px;width:239px;height:89px">
    <span class="logo__name">KESTREL</span>
    <span class="logo__sub">HAIR STUDIO</span>
  </div>

  <h2 class="services__title abs" style="left:258px;top:134px">SERVICES WE OFFER</h2>
  <ul class="services__list abs" style="left:258px;top:161px">
    <li><svg width="8" height="8" viewBox="0 0 8 8"><circle cx="4" cy="4" r="4" fill="#e9c9bf"/><path d="M2.2 4.1l1.2 1.1 2.4-2.4" stroke="#000" stroke-width="1" fill="none"/></svg>Mens &amp; Ladies Haircuts</li>
    <li><svg width="8" height="8" viewBox="0 0 8 8"><circle cx="4" cy="4" r="4" fill="#e9c9bf"/><path d="M2.2 4.1l1.2 1.1 2.4-2.4" stroke="#000" stroke-width="1" fill="none"/></svg>Style Cuts</li>
    <li><svg width="8" height="8" viewBox="0 0 8 8"><circle cx="4" cy="4" r="4" fill="#e9c9bf"/><path d="M2.2 4.1l1.2 1.1 2.4-2.4" stroke="#000" stroke-width="1" fill="none"/></svg>Colour Services</li>
    <li><svg width="8" height="8" viewBox="0 0 8 8"><circle cx="4" cy="4" r="4" fill="#e9c9bf"/><path d="M2.2 4.1l1.2 1.1 2.4-2.4" stroke="#000" stroke-width="1" fill="none"/></svg>Blowdry &amp; Styling</li>
    <li><svg width="8" height="8" viewBox="0 0 8 8"><circle cx="4" cy="4" r="4" fill="#e9c9bf"/><path d="M2.2 4.1l1.2 1.1 2.4-2.4" stroke="#000" stroke-width="1" fill="none"/></svg>Up Styles</li>
    <li><svg width="8" height="8" viewBox="0 0 8 8"><circle cx="4" cy="4" r="4" fill="#e9c9bf"/><path d="M2.2 4.1l1.2 1.1 2.4-2.4" stroke="#000" stroke-width="1" fill="none"/></svg>Perming</li>
    <li><svg width="8" height="8" viewBox="0 0 8 8"><circle cx="4" cy="4" r="4" fill="#e9c9bf"/><path d="M2.2 4.1l1.2 1.1 2.4-2.4" stroke="#000" stroke-width="1" fill="none"/></svg>Chemical straightening</li>
  </ul>

  <div class="promo" style="left:26px;top:319px;width:466px;height:67px">
    <span class="promo__amount">20% OFF</span>
    <span class="promo__text">Present this flyer to receive<br>any hair colour service</span>
  </div>

  <div class="photo photo--brunette" style="left:26px;top:402px;width:216px;height:234px" role="img" aria-label="Photo of shoulder-length brunette hair with loose waves"></div>
  <div class="photo photo--mens-side" style="left:259px;top:402px;width:233px;height:305px" role="img" aria-label="Photo of a men's short side-parted haircut with faded sides"></div>

  <div class="contact" style="left:26px;top:647px;width:216px;height:59px">
    <div class="contact__row" style="left:6px;top:9px">
      <svg width="14" height="14" viewBox="0 0 14 14"><circle cx="7" cy="7" r="7" fill="#fff"/><path d="M4.6 3.6l1.3 1.6-.7 1c.5 1 1.3 1.8 2.3 2.3l1-.7 1.6 1.3-.7 1.2c-2.8-.4-5.1-2.7-5.5-5.5z" fill="#000"/></svg>
      <span>472 083 56</span>
    </div>
    <div class="contact__social" style="left:115px;top:9px">
      <span>Follow us</span><span class="contact__dot"></span>
    </div>
    <div class="contact__row" style="left:6px;top:30px;align-items:flex-start">
      <svg width="14" height="14" viewBox="0 0 14 14"><circle cx="7" cy="7" r="7" fill="#fff"/><path d="M7 3a2.4 2.4 0 0 1 2.4 2.4C9.4 7.2 7 10.2 7 10.2S4.6 7.2 4.6 5.4A2.4 2.4 0 0 1 7 3z" fill="#000"/><circle cx="7" cy="5.4" r=".9" fill="#fff"/></svg>
      <span style="line-height:1.35">Shop 3/214 Garrow Street,<br>The Lindens, Harlow Bay 4812</span>
    </div>
  </div>
</section>

<section class="flyer flyer--back">
  <div class="flyer__sheet"></div>

  <div class="logo" style="left:26px;top:26px;width:233px;height:89px">
    <span class="logo__name">KESTREL</span>
    <span class="logo__sub">HAIR STUDIO</span>
  </div>

  <h2 class="deals__title abs" style="left:26px;top:136px">WEEKLY DEALS</h2>
  <p class="deals__feature abs" style="left:26px;top:165px"><b>Mens Day Wednesday</b><br><b class="deals__price">$19.00</b> Haircuts</p>
  <h3 class="deals__sub abs" style="left:26px;top:213px">Thursday Seniors Day</h3>

  <table class="price-table" style="left:26px;top:236px;width:233px">
    <tr><td>Shampoo, Ladies Haircut &amp; Blowdry</td><td class="price">$35</td></tr>
    <tr><td>Ladies Haircut &amp; Blowdry</td><td class="price">$30</td></tr>
    <tr><td>Shampoo &amp; Blowdry</td><td class="price">$27</td></tr>
    <tr><td>Perm (includes Trim &amp; Blowdry)</td><td class="price">$85</td></tr>
    <tr><td>Facial Waxing</td><td class="price">$10</td></tr>
  </table>

  <h3 class="deals__sub abs" style="left:26px;top:361px">FRIDAY HAPPY HOUR 3PM – 5PM</h3>
  <table class="price-table" style="left:26px;top:378px;width:233px">
    <tr><td>Shampoo, Blow dry &amp; Style</td><td class="price">$40</td></tr>
    <tr class="tall"><td>Shampoo, Mens Haircut &amp; Style<br>(Complimentary beverage on arrival)</td><td class="price">$29</td></tr>
  </table>

  <div class="photo photo--storefront" style="left:26px;top:446px;width:233px;height:190px" role="img" aria-label="Photo of the salon shopfront with a small café table, chairs and potted plant"></div>

  <div class="contact" style="left:26px;top:647px;width:233px;height:59px">
    <div class="contact__row" style="left:6px;top:9px">
      <svg width="14" height="14" viewBox="0 0 14 14"><circle cx="7" cy="7" r="7" fill="#fff"/><path d="M4.6 3.6l1.3 1.6-.7 1c.5 1 1.3 1.8 2.3 2.3l1-.7 1.6 1.3-.7 1.2c-2.8-.4-5.1-2.7-5.5-5.5z" fill="#000"/></svg>
      <span>472 083 56</span>
    </div>
    <div class="contact__social" style="left:115px;top:9px">
      <span>Follow us</span><span class="contact__dot"></span>
    </div>
    <div class="contact__row" style="left:6px;top:30px;align-items:flex-start">
      <svg width="14" height="14" viewBox="0 0 14 14"><circle cx="7" cy="7" r="7" fill="#fff"/><path d="M7 3a2.4 2.4 0 0 1 2.4 2.4C9.4 7.2 7 10.2 7 10.2S4.6 7.2 4.6 5.4A2.4 2.4 0 0 1 7 3z" fill="#000"/><circle cx="7" cy="5.4" r=".9" fill="#fff"/></svg>
      <span style="line-height:1.35">Shop 3/214 Garrow Street,<br>The Lindens, Harlow Bay 4812</span>
    </div>
  </div>

  <div class="photo photo--fade-back" style="left:277px;top:26px;width:215px;height:219px" role="img" aria-label="Photo of a men's textured crop seen from behind in the salon chair"></div>
  <div class="photo photo--fade-side" style="left:277px;top:257px;width:215px;height:219px" role="img" aria-label="Photo of a men's skin fade with a swept-back top"></div>
  <div class="photo photo--blonde" style="left:277px;top:487px;width:215px;height:219px" role="img" aria-label="Photo of sleek straight platinum blonde hair"></div>
</section>

</body>
</html>
```